The Quiet Harvest Book Cover

Cover for Multiauthor Ebook & Paper Print Book Cover

Book Title:
The Quiet Harvest: Lessons of Insight From A Circle of Mentors to Guide You Toward a Fuller Journey

This book will offer the wisdom and philosophies of a variety of different coaches to allow future clients to get a taste of you and your style and prepare them to work with you!

A coach does not fix you. Or heal you. They coach you - offer thoughts to ponder, guidance, techniques to try. All to help you plays and succeed at the game of life.

Each coach has their own personality, training, experience, method and philosophy they bring to the table. The underlying purpose is to guide you through the quiet harvest, to become the person you desire and aspire to be. Different coaches for different folks, yet they all have their own unique wisdom and special sauce to share.

This book is a collection of just that. A tasting of the wisdom and philosophies of a variety of different coaches for you to experience.

Types of Coaches: Clarity, Dreams, Goals, Motivation, Mindset,  Subconscious, Beliefs, Behavior, Accountability, Life, Wellness, Love & Dating, Relationships, Sex, Business, Career,  Executive,  Personal Development,  Writing, Wellness, Fitness, Parenting,  Style, Spirituality, Public Speaking, Financial,  Time management, Weight Loss, Running, Self esteem,  Tarot, Astrology, Enneagram, Soul path/ Dharma, Skills, Performance,  Speaking / Communication, Leadership, Shadow Work, Acting, Sports, ANY & ALL

Target Market(s)

Males or females looking for guidance and words of wisdom from an expert coach - maybe to find one that resonates with them to work with further. Ages 16 and up. Any Gender. International. Looking to improve their life!

Industry/Entity Type

Self Development, Wellness, Coaching, Personal Growth, Fitness, Spirituality, Business, Relationships

Font styles to use
Serif
Script

Colors
0054AA
0677BA
7BADD7
CADEEF
E8F1F8
FFF300
FFF600
FEFA6F
FFFEC7
FFFEE8

Requirements
Must have
• I am looking for a visually appealing, unique cover that encompasses the breadth and depth of the transformation that people can go through and inspires them to want to grow and change even more. I love when elegant and classic simplicity is combined with some kind of twist that catches the eye and provokes thought. I love complimentary fonts, colors, design elements. You can visit my Brindlemart Author Page - Dr. Marisol Pendergast Voyle to see my titles to see what I have liked! But I am also excited to see where you can make my vision even better!!
Nice to have
• Front Cover - Image, Title and Subtitle, The Lantern Publishing House, Spine - Title and Publishing House Logo, Back - Book Blurb, Authors Names, Info about Publishing House, ISBN Barcode
Should not have
• Anything too feminine or too masculine as I want to encourage coaches of all genders to participate.

```html
<!DOCTYPE html>
<html lang="en">
<head>
<meta charset="utf-8">
<title>The Quiet Harvest — Book Cover</title>
<link href="https://fonts.googleapis.com/css2?family=Allura&family=Cinzel:wght@700&family=Cormorant+Garamond:wght@500&family=Inter:wght@400&display=swap" rel="stylesheet">
<style>
  :root {
    --stage: #9a9a9a;
    --cover-light: #bebebc;
    --cover-mid: #b1b1af;
    --cover-dark: #a4a4a2;
    --ink: #141414;
    --gold: #d9a42a;
    --white: #ffffff;
    --wing-dark: #1c1410;
    --wing-gold: #f1bb34;
  }
  html, body {
    margin: 0;
    padding: 0;
    width: 1200px;
    height: 1200px;
    overflow: hidden;
    background: var(--stage);
  }
  .canvas {
    position: relative;
    width: 1200px;
    height: 1200px;
    background: var(--stage);
  }
  .cover {
    position: absolute;
    left: 240px;
    top: 60px;
    width: 720px;
    height: 1080px;
    overflow: hidden;
    background: radial-gradient(ellipse at 50% 55%, var(--cover-light) 0%, var(--cover-mid) 55%, var(--cover-dark) 100%);
    box-shadow: 0 10px 40px rgba(0,0,0,0.25);
  }
  .title-flourish {
    position: absolute;
    left: 0;
    top: 0;
    width: 720px;
    height: 460px;
  }
  .title-the {
    position: absolute;
    left: 80px;
    top: 22px;
    font-family: "Allura", cursive;
    font-size: 150px;
    line-height: 1;
    color: var(--white);
  }
  .title-main {
    position: absolute;
    left: 120px;
    top: 150px;
    margin: 0;
    font-family: "Cinzel", serif;
    font-weight: 700;
    font-size: 128px;
    letter-spacing: 4px;
    line-height: 1;
    color: var(--ink);
    text-shadow: 2px 2px 0 var(--gold);
    transform: rotate(-5deg);
    transform-origin: left bottom;
  }
  .title-harvest {
    position: absolute;
    left: 190px;
    top: 292px;
    font-family: "Allura", cursive;
    font-size: 150px;
    line-height: 1;
    color: var(--white);
  }
  .sparkle {
    position: absolute;
    left: 452px;
    top: 282px;
    width: 30px;
    height: 30px;
    border-radius: 50%;
    background: radial-gradient(circle, #ffffff 0%, rgba(255,255,255,0.7) 25%, rgba(255,255,255,0) 70%);
  }
  .butterfly-art {
    position: absolute;
    left: 80px;
    top: 480px;
    width: 560px;
    height: 340px;
    background: radial-gradient(closest-side, var(--wing-gold) 0%, #a0702a 30%, var(--wing-dark) 62%, rgba(28,20,16,0.45) 85%, rgba(28,20,16,0) 100%);
  }
  .subtitle {
    position: absolute;
    left: 90px;
    top: 855px;
    width: 540px;
    margin: 0;
    font-family: "Cormorant Garamond", serif;
    font-weight: 500;
    font-size: 24px;
    line-height: 1.15;
    letter-spacing: 1px;
    text-transform: uppercase;
    text-align: center;
    color: var(--white);
  }
  .publisher {
    position: absolute;
    left: 0;
    top: 1010px;
    width: 720px;
    margin: 0;
    font-family: "Inter", sans-serif;
    font-size: 20px;
    text-align: center;
    color: var(--white);
  }
  .publisher .dot {
    display: inline-block;
    width: 5px;
    height: 5px;
    border-radius: 50%;
    background: var(--white);
    vertical-align: middle;
    margin: 0 8px;
  }
</style>
</head>
<body>
<main class="canvas">
  <section class="cover" aria-label="Front cover: The Quiet Harvest">
    <svg class="title-flourish" viewBox="0 0 720 460" aria-hidden="true">
      <path d="M0 130 C 35 130, 70 128, 96 120" fill="none" stroke="#ffffff" stroke-width="2.5"/>
      <path d="M590 400 C 630 392, 680 378, 720 368" fill="none" stroke="#ffffff" stroke-width="2.5"/>
    </svg>
    <div class="title-the">the</div>
    <h1 class="title-main">QUIET</h1>
    <div class="title-harvest">harvest</div>
    <div class="sparkle" aria-hidden="true"></div>

    <div class="butterfly-art" role="img" aria-label="Photograph of a butterfly with black and white patterned wings and golden-yellow inner hindwings, wings spread open"></div>

    <p class="subtitle">Lessons of insight from a circle of mentors to change your heart, mind, body &amp; soul.</p>

    <p class="publisher"><span class="dot"></span>The Lantern Publishing House<span class="dot"></span></p>
  </section>
</main>
</body>
</html>
```